Dunmore Roofing

Want a professional looking business card

Industry/Entity Type

Business

Contact Information for Business Card

Paul Dunmore ( Owner) paul@dunmoreroofing-example.com, www.dunmoreroofing-example.com, Adress: 4172 Township road 43 Elmvale Ridge,ON K9X4T2

```html
<!DOCTYPE html>
<html lang="en">
<head>
<meta charset="UTF-8">
<title>Dunmore Roofing – Business Card</title>
<link rel="stylesheet" href="https://fonts.googleapis.com/css2?family=Open+Sans:wght@400;600;700;800&display=swap">
<style>
  :root {
    --backdrop: #2b2b2d;
    --brand-blue: #1c4a94;
    --brand-blue-dark: #163d7d;
    --card-white: #ffffff;
    --band-grey: #8a8b8d;
    --stripe-grey: #e7e7e8;
    --rule-grey: #c4c4c6;
    --text-grey: #55575a;
  }
  * { box-sizing: border-box; margin: 0; padding: 0; }
  html, body {
    width: 1200px; height: 900px; overflow: hidden;
    background: var(--backdrop);
    font-family: "Open Sans", Arial, sans-serif;
  }
  .canvas { position: relative; width: 1200px; height: 900px; }

  .card {
    position: absolute;
    width: 520px; height: 298px;
    border-radius: 18px;
    overflow: hidden;
  }

  /* Back of card */
  .card-back { left: 70px; top: 120px; background: var(--brand-blue); }
  .card-back .world-map {
    position: absolute; left: 60px; top: 30px; width: 400px; height: 230px;
    background: radial-gradient(ellipse at center, rgba(255,255,255,0.07), rgba(255,255,255,0) 70%);
  }
  .card-back .wordmark {
    position: absolute; left: 0; right: 0; top: 92px;
    text-align: center; color: var(--card-white);
    font-weight: 800; font-size: 38px; line-height: 1.05; letter-spacing: 2px;
    text-transform: uppercase;
  }
  .card-back .web-line {
    position: absolute; left: 30px; right: 30px; bottom: 34px;
    display: flex; align-items: center; gap: 10px;
    color: var(--card-white); font-size: 12.5px;
  }
  .card-back .web-line .rule { flex: 1; height: 1px; background: rgba(255,255,255,0.7); }

  /* Front of card */
  .card-front { left: 610px; top: 480px; background: var(--card-white); }
  .card-front .shapes { position: absolute; inset: 0; }
  .card-front .wordmark {
    position: absolute; left: 40px; top: 108px;
    color: var(--brand-blue);
    font-weight: 800; font-size: 30px; line-height: 1.05; letter-spacing: 1.5px;
    text-transform: uppercase;
  }
  .card-front .contact-block {
    position: absolute; right: 16px; top: 92px; text-align: right;
    color: var(--text-grey);
  }
  .contact-block .person-name { color: var(--brand-blue); font-weight: 700; font-size: 17px; }
  .contact-block .person-role { font-size: 11.5px; margin-bottom: 10px; margin-right: 24px; }
  .contact-block .contact-line {
    display: flex; justify-content: flex-end; align-items: center; gap: 8px;
    font-size: 11.5px; line-height: 17px;
  }
  .contact-line .icon {
    width: 14px; height: 14px; border-radius: 3px; background: var(--brand-blue);
    display: inline-flex; align-items: center; justify-content: center;
  }
  .card-front .address {
    position: absolute; left: 14px; bottom: 6px;
    color: var(--card-white); font-size: 12px;
  }
</style>
</head>
<body>
<main class="canvas">

  <section class="card card-back" aria-label="Business card back">
    <div class="world-map" role="img" aria-label="Faint dotted world map backdrop"></div>
    <div class="wordmark">Dunmore<br>Roofing</div>
    <div class="web-line">
      <span class="rule"></span>
      <span class="web-address">www.dunmoreroofing-example.com</span>
      <span class="rule"></span>
    </div>
  </section>

  <section class="card card-front" aria-label="Business card front">
    <svg class="shapes" viewBox="0 0 520 298" width="520" height="298" aria-hidden="true">
      <polygon points="298,0 316,0 266,182 248,182" fill="var(--stripe-grey)"/>
      <line x1="60" y1="258" x2="520" y2="222" stroke="var(--rule-grey)" stroke-width="0.8"/>
      <polygon points="386,246 520,246 520,298 366,298" fill="var(--band-grey)"/>
      <polygon points="0,272 376,272 366,298 0,298" fill="var(--brand-blue)"/>
      <rect x="392" y="254" width="8" height="8" fill="var(--card-white)"/>
    </svg>

    <div class="wordmark">Dunmore<br>Roofing</div>

    <div class="contact-block">
      <div class="person-name">Paul Dunmore</div>
      <div class="person-role">Owner</div>
      <div class="contact-line">
        <span>(613) 555-0148</span>
        <span class="icon">
          <svg width="9" height="9" viewBox="0 0 10 10"><path d="M2 1l2 2-1 1.2c.6 1.2 1.6 2.2 2.8 2.8L7 6l2 2-1.2 1.4C4.5 9.2.8 5.5.6 2.2z" fill="#fff"/></svg>
        </span>
      </div>
      <div class="contact-line">
        <span>paul@dunmoreroofing-example.com</span>
        <span class="icon">
          <svg width="9" height="9" viewBox="0 0 10 10"><rect x="0.5" y="2" width="9" height="6" fill="none" stroke="#fff"/><path d="M0.5 2l4.5 3.5L9.5 2" fill="none" stroke="#fff"/></svg>
        </span>
      </div>
      <div class="contact-line">
        <span>www.dunmoreroofing-example.com</span>
        <span class="icon">
          <svg width="9" height="9" viewBox="0 0 10 10"><circle cx="5" cy="5" r="4" fill="none" stroke="#fff"/><ellipse cx="5" cy="5" rx="1.8" ry="4" fill="none" stroke="#fff" stroke-width="0.8"/><line x1="1" y1="5" x2="9" y2="5" stroke="#fff" stroke-width="0.8"/></svg>
        </span>
      </div>
    </div>

    <div class="address">4172 Township road 43, Elmvale Ridge, ON K9X4T2</div>
  </section>

</main>
</body>
</html>
```